Northfield Builders Guild Business card

We are looking for a new business card design with photo included.
Our business is a nonprofit construction contractor membership organization. We offer business education, assist with business setup and licensing, provide safety training, and provide a member directory.
URL: www.builderslinkguild.org
Color code:
CMYK: 0 cyan, 42 magenta, 100 yellow, 0 black for Print.
Hexidecimal: #FF9900
RGB: R 255; G 153; B 0

```html
<!DOCTYPE html>
<html lang="en">
<head>
<meta charset="utf-8">
<title>Northfield Builders Guild – Business Card</title>
<link rel="stylesheet" href="https://fonts.googleapis.com/css2?family=Montserrat:wght@400;500;800&display=swap">
<style>
  :root {
    --orange: #ff9900;
    --charcoal: #363435;
    --ink: #3f3d3e;
    --paper: #ffffff;
    --backdrop: #e6e6e6;
    --rule: #555355;
  }
  * { box-sizing: border-box; margin: 0; padding: 0; }
  html, body { width: 1200px; height: 1200px; overflow: hidden; }
  body {
    background: var(--backdrop);
    font-family: "Montserrat", sans-serif;
    position: relative;
  }
  .card {
    position: absolute;
    left: 250px;
    width: 700px;
    border-radius: 22px;
    overflow: hidden;
  }
  .card-front { top: 160px; height: 385px; background: var(--paper); color: var(--ink); }
  .card-back  { top: 645px; height: 400px; background: var(--charcoal); }

  .brand {
    position: absolute;
    display: flex;
    align-items: center;
    gap: 10px;
    font-weight: 800;
    letter-spacing: -0.3px;
    line-height: 1;
  }
  .brand-mark { width: 14px; height: 14px; background: var(--orange); flex: none; }
  .card-front .brand { right: 40px; top: 80px; font-size: 25px; color: var(--ink); }
  .card-back .brand {
    left: 0; right: 0; top: 180px;
    justify-content: center;
    font-size: 36px; color: var(--paper);
  }

  .accent-bar { position: absolute; left: 0; top: 225px; width: 17px; height: 44px; background: var(--orange); }
  .person { position: absolute; left: 47px; top: 224px; }
  .person-name { font-size: 24px; font-weight: 500; letter-spacing: 0.4px; line-height: 1.1; }
  .person-title { font-size: 17px; color: var(--orange); line-height: 1.25; }
  .divider { position: absolute; left: 47px; right: 47px; top: 281px; height: 1px; background: var(--rule); }

  .contact-list { position: absolute; left: 47px; top: 293px; list-style: none; font-size: 16px; }
  .contact-list li { display: flex; align-items: center; gap: 8px; height: 20px; }
  .contact-list svg { width: 13px; height: 13px; fill: var(--orange); flex: none; }

  .address {
    position: absolute; right: 40px; top: 296px;
    font-size: 16px; font-style: normal; text-align: right; line-height: 20px;
  }

  .web {
    position: absolute; left: 0; right: 0; top: 330px;
    text-align: center; font-size: 16px; font-weight: 500; color: var(--orange);
  }
</style>
</head>
<body>

<section class="card card-front" aria-label="Business card front">
  <div class="brand"><span class="brand-mark"></span>Northfield Builders Guild</div>

  <span class="accent-bar"></span>
  <div class="person">
    <p class="person-name">DANIEL REEVES</p>
    <p class="person-title">President</p>
  </div>
  <span class="divider"></span>

  <ul class="contact-list">
    <li>
      <svg viewBox="0 0 16 16" aria-hidden="true"><path d="M3.6 1l2.4 3-1.5 1.8c.8 1.9 2.3 3.4 4.2 4.2L10.5 8.5l3 2.4-1.2 3C7 13.5 2.5 9 2.1 3.7z"/></svg>
      (555) 214-3380
    </li>
    <li>
      <svg viewBox="0 0 16 16" aria-hidden="true"><path d="M4 0h8a1 1 0 0 1 1 1v14a1 1 0 0 1-1 1H4a1 1 0 0 1-1-1V1a1 1 0 0 1 1-1zm1 2v10h6V2zm3 11a1 1 0 1 0 0 2 1 1 0 0 0 0-2z"/></svg>
      555.307.4412
    </li>
    <li>
      <svg viewBox="0 0 16 16" aria-hidden="true"><path d="M1 4h14v9H1zm1.5 1L8 9l5.5-4z"/></svg>
      support@nbguild.org
    </li>
    <li>
      <svg viewBox="0 0 16 16" aria-hidden="true"><path d="M8 1a7 7 0 1 0 0 14A7 7 0 0 0 8 1zm0 1.6c.9 1 1.5 2.4 1.7 4.4H6.3C6.5 5 7.1 3.6 8 2.6zM6.3 8.5h3.4c-.2 2-.8 3.4-1.7 4.4-.9-1-1.5-2.4-1.7-4.4z"/></svg>
      builderslinkguild.org
    </li>
  </ul>

  <address class="address">
    2400 Harbor Ridge Rd.,<br>
    Suite #210<br>
    Millbrook, OR 97000
  </address>
</section>

<section class="card card-back" aria-label="Business card back">
  <div class="brand"><span class="brand-mark"></span>Northfield Builders Guild</div>
  <p class="web">www.builderslinkguild.org</p>
</section>

</body>
</html>
```